Commercial and Residential Paint Contractor needs website

We need a website for our residential painting, multi-family painting and commercial painting company. We paint interior and exterior of houses, apartments and commercial buildings. I would like an about us page, residential page, multi family page, commercial page and contact us. Need keywords added to website for seo opitimazation. I like this website https://www.wallcraftcrew.com/

Target Market(s)

General Contractors and commercial property managers

Coding

Coded - Design and coding required

Number of Pages Required

5+ page

Font styles to use
Sans Serif

Requirements
Must have
• I need SEO keywords on pages

```html
<!DOCTYPE html>
<html lang="en">
<head>
<meta charset="utf-8">
<title>Crestline Painting – Residential, Multi-Family &amp; Commercial Painting</title>
<link href="https://fonts.googleapis.com/css2?family=Roboto:ital,wght@0,400;0,500;0,700;0,900;1,400&display=swap" rel="stylesheet">
<style>
:root{
  --blue:#1a4f94;
  --red:#d0213a;
  --ink:#333;
  --muted:#555;
  --line:#dcdcdc;
  --footer:#222;
  --white:#fff;
}
*{box-sizing:border-box;margin:0;padding:0}
html,body{width:1200px;height:4276px;overflow:hidden}
body{font-family:'Roboto',sans-serif;color:var(--ink);background:var(--white);position:relative}
.abs{position:absolute}
a{color:inherit;text-decoration:none}

/* top bar */
.topbar{left:0;top:0;width:1200px;height:30px;background:var(--blue);color:#fff;font-size:13px;font-weight:500;padding:8px 0 0 66px}
.topbar .social{position:absolute;right:70px;top:7px;display:flex;gap:10px}
.topbar .social span{width:15px;height:15px;border:2px solid #fff;border-radius:2px}

/* header */
.header{left:0;top:30px;width:1200px;height:106px;background:#fff;box-shadow:0 2px 4px rgba(0,0,0,.08)}
.brand{position:absolute;left:92px;top:35px;display:flex;align-items:center;gap:10px;font-weight:900;font-size:30px;color:var(--blue);letter-spacing:.5px}
.brand i{width:14px;height:14px;background:var(--red);display:block}
.nav{position:absolute;right:88px;top:44px;display:flex;gap:40px;font-size:15px;color:#222}
.nav .active{color:var(--blue)}

/* hero */
.hero{left:0;top:136px;width:1200px;height:570px;background:linear-gradient(100deg,#9ec7e6 0%,#c9b59a 30%,#e6e2dc 55%,#d9cfc3 100%)}
.hero-splash{left:648px;top:236px;width:552px;height:400px;background:var(--red)}
.hero-title{left:648px;top:316px;width:552px;text-align:center;color:#fff;font-weight:700;font-size:34px;line-height:40px}
.hero-title strong{display:block;color:var(--blue);font-size:46px;line-height:56px;font-weight:900;margin-top:6px}
.dots{left:555px;top:663px;display:flex;gap:16px}
.dots span{width:20px;height:8px;background:var(--red)}
.dots span:first-child{background:var(--blue)}

/* section headings */
.heading{font-weight:900;color:var(--blue);font-size:42px;letter-spacing:.5px;line-height:50px}
.btn{background:var(--red);color:#fff;font-weight:700;font-size:17px;text-align:center}

/* about */
.about-text{left:66px;top:942px;width:540px;font-size:14.5px;line-height:26.5px;color:var(--muted)}
.contact-row{display:flex;gap:22px;align-items:flex-start}
.contact-row .label{color:var(--blue);font-weight:500;font-size:15px}
.contact-row .value{font-size:14.5px;color:var(--ink);margin-top:4px}
.about-photo{left:606px;top:797px;width:594px;height:415px;background:linear-gradient(135deg,#f0ece4,#e2d796 45%,#b8bcc4 70%,#6b7689)}

/* gallery */
.gallery{left:66px;top:1486px;width:1068px;height:526px;display:grid;grid-template-columns:repeat(4,1fr);grid-template-rows:repeat(2,1fr)}
.gallery div{position:relative}
.g1{background:linear-gradient(#8bb7e0,#a89a86 55%,#6b7a4a)}
.g2{background:linear-gradient(#e8e4de,#c7c0b6 60%,#5b4a3c)}
.g3{background:linear-gradient(#ece9e4,#b8b4ae 60%,#4a4848)}
.g4{background:linear-gradient(#3d3f46,#4c5c86 40%,#9c9c9e)}
.g5{background:linear-gradient(#ece7df,#d4ccc0 60%,#6b5a4a)}
.g6{background:linear-gradient(#3f76b8,#5485c0 60%,#3a6aa2)}
.g6::before{content:"";position:absolute;inset:12px;border:3px solid #fff}
.g6::after{content:"+";position:absolute;left:0;right:0;top:108px;text-align:center;color:#fff;font-size:40px;font-weight:700}
.g7{background:linear-gradient(90deg,#5c4a36,#9c7a52 50%,#6b5640)}
.g8{background:linear-gradient(#f2efea,#d8d2c8 60%,#5d4c3e)}

/* services */
.service{width:300px;text-align:center}
.service .art{width:266px;height:166px;margin:0 auto;background:var(--red)}
.service h3{color:var(--blue);font-weight:500;font-size:21px;line-height:24px;margin-top:46px}

/* testimonials */
.clients{left:0;top:2709px;width:1200px;height:608px;background:linear-gradient(120deg,#1f4c9a 0%,#5b82c4 20%,#c81f2c 45%,#e9d640 65%,#e78c20 80%,#b5121b 100%)}
.clients-title{left:0;top:2738px;width:1200px;text-align:center;color:#fff;font-weight:900;font-size:42px;line-height:50px}
.clients-sub{left:220px;top:2806px;width:760px;text-align:center;color:#fff;font-style:italic;font-size:14.5px;line-height:20px}
.card{top:2951px;height:249px;background:#fff;text-align:center;padding-top:75px}
.card.current{border:3px solid var(--red)}
.card h4{font-weight:500;font-size:16.5px;color:#111}
.card p{font-style:italic;font-size:14.5px;line-height:23px;color:var(--muted);margin:30px auto 0;width:290px}
.avatar{top:2896px;width:106px;height:106px;border-radius:50%;background:linear-gradient(#d8d8d8,#9a9a9a);border:4px solid #fff}
.avatar.current{border-color:var(--red)}
.cdots{left:568px;top:3253px;display:flex;gap:14px}
.cdots span{width:14px;height:14px;border-radius:50%;border:2px solid #fff}
.cdots span:first-child{border-color:var(--red)}

/* find us */
.find-text{left:66px;top:3470px;width:420px;font-size:13.5px;line-height:23px;color:var(--muted)}
.info{left:100px;display:flex;gap:28px;align-items:flex-start}
.info .label{color:var(--blue);font-weight:500;font-size:15px}
.info .value{font-size:15px;color:var(--ink);margin-top:4px}
.field{border:1px solid var(--line);font-size:13.5px;color:#777;padding:14px 16px}

/* footer */
.footer{left:0;top:3889px;width:1200px;height:387px;background:var(--footer);color:#fff}
.f-brand{position:absolute;left:92px;top:48px;display:flex;align-items:center;gap:9px;font-weight:900;font-size:26px}
.f-brand i{width:13px;height:13px;background:#fff;display:block}
.f-about{position:absolute;left:92px;top:168px;width:315px;text-align:center;font-size:13px;line-height:20px}
.f-col{position:absolute;top:60px}
.f-col h5{color:var(--red);font-weight:500;font-size:16px;margin-bottom:14px}
.f-col li{list-style:none;font-size:15px;font-weight:500;line-height:38px}
.f-col li::before{content:"» ";font-weight:700}
.newsletter{position:absolute;left:817px;top:98px;width:295px;height:50px;display:flex}
.newsletter span{flex:1;background:#fff;color:#555;font-size:13px;padding:18px 16px}
.newsletter b{width:58px;background:var(--blue);display:flex;align-items:center;justify-content:center}
.f-social{position:absolute;left:856px;top:203px;display:flex;gap:18px}
.f-social span{width:29px;height:29px;border:3px solid #fff;border-radius:3px}
.f-rule{position:absolute;left:90px;top:327px;width:1022px;height:1px;background:#555}
.copy{position:absolute;left:0;top:350px;width:1200px;text-align:center;font-size:13px;font-weight:500}
</style>
</head>
<body>

<div class="abs topbar">Welcome Our Website
  <div class="social"><span></span><span></span><span></span><span></span><span></span></div>
</div>

<header class="abs header">
  <div class="brand"><i></i>CRESTLINE PAINTING</div>
  <nav class="nav"><a class="active">Home</a><a>About Us</a><a>Services</a><a>Gallery</a><a>Blog</a><a>Contact Us</a></nav>
</header>

<section class="abs hero" role="img" aria-label="Painter holding brushes in a freshly painted room"></section>
<div class="abs hero-splash" role="img" aria-label="Red paint splash behind the welcome text"></div>
<h1 class="abs hero-title">WELCOME FOR<strong>CRESTLINE PAINTING</strong></h1>
<div class="abs dots"><span></span><span></span><span></span></div>

<!-- about -->
<h2 class="abs heading" style="left:66px;top:864px">ABOUT US</h2>
<p class="abs about-text">We are family owned and operated with over 10 years' experience. We pride our self in performing to the highest degree of workmanship standards. Crestline Painting is your best choice for commercial, residential and multi-family painting in the DFW/Forth Worth area. Our experienced estimators will meet with you and customize a proposal to meet your needs. They will stay with you from the beginning of the project to the end, making sure you are 100% satisfied.</p>
<div class="abs contact-row" style="left:100px;top:1146px">
  <svg width="30" height="30" viewBox="0 0 24 24"><path fill="#d0213a" d="M6.6 10.8a15.1 15.1 0 0 0 6.6 6.6l2.2-2.2c.3-.3.7-.4 1-.2 1.1.4 2.3.6 3.6.6.6 0 1 .4 1 1V20c0 .6-.4 1-1 1A17 17 0 0 1 3 4c0-.6.4-1 1-1h3.5c.6 0 1 .4 1 1 0 1.3.2 2.5.6 3.6.1.3 0 .7-.2 1z"/></svg>
  <div><div class="label">PHONE</div><div class="value">(555)-210-0199, (555)-210-0199</div></div>
</div>
<div class="abs about-photo" role="img" aria-label="Hand rolling yellow paint in a tray"></div>

<!-- gallery -->
<h2 class="abs heading" style="left:64px;top:1376px">GALLERY</h2>
<div class="abs btn" style="left:971px;top:1374px;width:164px;height:42px;line-height:42px">VIEW ALL</div>
<div class="abs gallery">
  <div class="g1" role="img" aria-label="Exterior of a painted house"></div>
  <div class="g2" role="img" aria-label="White kitchen interior"></div>
  <div class="g3" role="img" aria-label="Bright living room"></div>
  <div class="g4" role="img" aria-label="Gym with mural wall"></div>
  <div class="g5" role="img" aria-label="Kitchen island with pendant lights"></div>
  <div class="g6" role="img" aria-label="House exterior, selected"></div>
  <div class="g7" role="img" aria-label="Reclaimed wood feature wall"></div>
  <div class="g8" role="img" aria-label="Kitchen with pendant lights"></div>
</div>

<!-- services -->
<h2 class="abs heading" style="left:65px;top:2174px">OUR SERVICES</h2>
<div class="abs service" style="left:74px;top:2291px"><div class="art" role="img" aria-label="House icon on a red paint splash"></div><h3>HOUSE</h3></div>
<div class="abs service" style="left:449px;top:2291px"><div class="art" role="img" aria-label="Apartment icon on a red paint splash"></div><h3>APARTMENT</h3></div>
<div class="abs service" style="left:828px;top:2291px"><div class="art" role="img" aria-label="Commercial building icon on a red paint splash"></div><h3 style="margin-top:34px">COMMERCIAL<br>BUILDING</h3></div>
<div class="abs btn" style="left:518px;top:2578px;width:163px;height:42px;line-height:42px">VIEW ALL</div>

<!-- testimonials -->
<section class="abs clients" role="img" aria-label="Open cans of colourful paint"></section>
<h2 class="abs clients-title">WHAT CLIENT SAY</h2>
<p class="abs clients-sub">There are many variations of passages of Lorem Ipsum available, but the majority have suffered alteration in some form, by injected humour, or randomised words</p>
<div class="abs card" style="left:70px;width:343px"><h4>OWEN HALE</h4><p>There are many variations of passages of Lorem Ipsum available, but the majority have suffered alteration in some form, by injected humour, or randomised words</p></div>
<div class="abs card current" style="left:430px;width:340px"><h4>LUCAS BRENT</h4><p>There are many variations of passages of Lorem Ipsum available, but the majority have suffered alteration in some form, by injected humour, or randomised words</p></div>
<div class="abs card" style="left:787px;width:343px"><h4>DARA QUILL</h4><p>There are many variations of passages of Lorem Ipsum available, but the majority have suffered alteration in some form, by injected humour, or randomised words</p></div>
<div class="abs avatar" style="left:189px" role="img" aria-label="Client portrait"></div>
<div class="abs avatar current" style="left:547px" role="img" aria-label="Client portrait"></div>
<div class="abs avatar" style="left:906px" role="img" aria-label="Client portrait"></div>
<div class="abs cdots"><span></span><span></span><span></span></div>

<!-- find us -->
<h2 class="abs heading" style="left:64px;top:3398px">IT'S EASY TO FIND US</h2>
<p class="abs find-text">It is a long established fact that a reader will be distracted by the readable content of a page when looking at its layout. The point of using Lorem Ipsum is that it has a more-or-less normal distribution of letters</p>
<div class="abs info" style="top:3594px">
  <svg width="38" height="34" viewBox="0 0 38 34"><path fill="#1a4f94" d="M0 10l11-4v28L0 34zM13 6l12 4v24l-12-4zM27 10l11-4v24l-11 4z"/><circle cx="19" cy="10" r="8" fill="#1a4f94" stroke="#fff" stroke-width="2"/><circle cx="19" cy="10" r="3" fill="#fff"/></svg>
  <div><div class="label">ADDRESS</div><div class="value">418 Maple Court, Cedar Hollow, TX 75001</div></div>
</div>
<div class="abs info" style="top:3666px">
  <svg width="38" height="34" viewBox="0 0 24 24"><path fill="#1a4f94" d="M6.6 10.8a15.1 15.1 0 0 0 6.6 6.6l2.2-2.2c.3-.3.7-.4 1-.2 1.1.4 2.3.6 3.6.6.6 0 1 .4 1 1V20c0 .6-.4 1-1 1A17 17 0 0 1 3 4c0-.6.4-1 1-1h3.5c.6 0 1 .4 1 1 0 1.3.2 2.5.6 3.6.1.3 0 .7-.2 1z"/></svg>
  <div><div class="label">PHONE</div><div class="value">(555)-210-0199, (555)-210-0199</div></div>
</div>
<div class="abs info" style="top:3740px">
  <svg width="38" height="28" viewBox="0 0 38 28"><rect width="38" height="28" rx="3" fill="#1a4f94"/><path d="M2 3l17 13L36 3" fill="none" stroke="#fff" stroke-width="2.5"/></svg>
  <div><div class="label">EMAIL</div><div class="value">hello@crestlinepainting.com</div></div>
</div>
<div class="abs field" style="left:533px;top:3496px;width:295px;height:47px">Name</div>
<div class="abs field" style="left:842px;top:3496px;width:293px;height:47px">Email</div>
<div class="abs field" style="left:533px;top:3559px;width:602px;height:47px">Subject</div>
<div class="abs field" style="left:533px;top:3624px;width:602px;height:116px">Message</div>
<div class="abs btn" style="left:971px;top:3758px;width:164px;height:43px;line-height:43px;font-size:15px">SEND</div>

<!-- footer -->
<footer class="abs footer">
  <div class="f-brand"><i></i>CRESTLINE PAINTING</div>
  <p class="f-about">It is a long established fact that a reader will be distracted by the readable content of a page when looking at its layout. The point of using Lorem Ipsum is that it has a more-or-less normal distribution of letters</p>
  <div class="f-col" style="left:460px"><h5>LINKS</h5><ul><li>Home</li><li>About Us</li><li>Services</li><li>Gallery</li><li>Blog</li><li>Contact Us</li></ul></div>
  <div class="f-col" style="left:599px"><h5>SERVICES</h5><ul><li>Houses</li><li>Apartments</li><li>Commercial Buildings</li></ul></div>
  <div class="f-col" style="left:815px"><h5>LATEST NEWS</h5></div>
  <div class="newsletter"><span>ENTER EMAIL</span><b><svg width="24" height="24" viewBox="0 0 24 24"><circle cx="10" cy="10" r="7" fill="none" stroke="#fff" stroke-width="3"/><path d="M15 15l7 7" stroke="#fff" stroke-width="3.5"/></svg></b></div>
  <div class="f-social"><span></span><span></span><span></span><span></span><span></span></div>
  <div class="f-rule"></div>
  <p class="copy">Copyright © 2020 CRESTLINE PAINTING - All Rights Reserved.</p>
</footer>

</body>
</html>
```